Business card por a urban DJ, up scale audience target

Need a sober design, modern, conservative colors but i can consider some options, y play rnb, hip hop, EDM and top40.

Business card for contact and personal info, double sided, use logo attrached please; im 42 so i need a card acording to my age an target audience.

Target Market(s)

Adult people, up scale audience

Industry/Entity Type

Music Download

Contact Information for Business Card

Cel (318) 4207265518 www.lumadrift.com

Requirements
Must have
• open mind
Nice to have
• open mind
Should not have
• DJ

```html
<!DOCTYPE html>
<html lang="en">
<head>
<meta charset="utf-8">
<title>Lumadrift — Business Card</title>
<link href="https://fonts.googleapis.com/css2?family=Jost:wght@400;500;700&display=swap" rel="stylesheet">
<style>
  :root {
    --backdrop: #3a3d42;
    --card-light: #fbfbfb;
    --card-dark: #1c1c1c;
    --ink: #161616;
    --ink-soft: #5a5a5a;
    --ink-light: #ffffff;
  }
  * { margin: 0; padding: 0; box-sizing: border-box; }
  html, body {
    width: 1200px;
    height: 750px;
    overflow: hidden;
  }
  body {
    background: var(--backdrop);
    font-family: "Jost", sans-serif;
    position: relative;
  }
  .card {
    position: absolute;
    top: 228px;
    width: 462px;
    height: 262px;
  }
  .card--front {
    left: 124px;
    background: var(--card-light);
    color: var(--ink);
  }
  .card--back {
    left: 618px;
    background: var(--card-dark);
    color: var(--ink-light);
  }
  .brand {
    position: absolute;
    display: flex;
    align-items: center;
    gap: 10px;
    font-weight: 700;
    letter-spacing: 2px;
    line-height: 1;
  }
  .brand__mark {
    display: block;
    background: currentColor;
  }
  .card--front .brand {
    left: 0;
    right: 0;
    top: 52px;
    justify-content: center;
    font-size: 72px;
  }
  .card--front .brand__mark { width: 22px; height: 22px; }
  .holder {
    position: absolute;
    left: 0;
    right: 0;
    top: 172px;
    text-align: center;
    font-size: 19px;
    font-weight: 500;
    letter-spacing: 0.2px;
  }
  .holder__role {
    font-weight: 400;
    font-size: 16px;
    color: var(--ink-soft);
  }
  .contact {
    position: absolute;
    left: 0;
    right: 0;
    top: 204px;
    text-align: center;
    font-size: 16px;
    color: var(--ink-soft);
  }
  .contact__sep { margin: 0 6px; }
  .card--back .brand {
    right: 26px;
    top: 160px;
    font-size: 44px;
    gap: 7px;
  }
  .card--back .brand__mark { width: 14px; height: 14px; }
  .back-url {
    position: absolute;
    right: 26px;
    top: 236px;
    width: 122px;
    text-align: center;
    font-size: 7.5px;
    font-weight: 700;
    letter-spacing: 1.6px;
  }
</style>
</head>
<body>
  <section class="card card--front">
    <div class="brand"><span class="brand__mark"></span>LUMA</div>
    <p class="holder">DARIO VANCE - <span class="holder__role">CEO/FOUNDER</span></p>
    <p class="contact">(318) 4207265518<span class="contact__sep">|</span>www.lumadrift.com</p>
  </section>

  <section class="card card--back">
    <div class="brand"><span class="brand__mark"></span>LUMA</div>
    <p class="back-url">WWW.LUMADRIFT.COM</p>
  </section>
</body>
</html>
```